Need a website where people can find information about the newly formed Northmere Valuation Oversight Board. Soon after, we will need a place to publish our findings as we audit each municipality in the State of Wisconsin. I have a logo (designed by Artwell Hub), a MS Word document showing the content and a set of images to choose from that we can purchase from Pixmarla.com (found here https://www.pixmarla.com/collaboration/boards/-Xq7TbLwRmNoPzYkAuH-Jd)

```html
<!DOCTYPE html>
<html lang="en">
<head>
<meta charset="utf-8">
<title>Northmere Valuation Oversight Board – Non-Uniform Property Tax Problem</title>
<link rel="stylesheet" href="https://fonts.googleapis.com/css2?family=Roboto:wght@400;500;700&family=Work+Sans:wght@800&display=swap">
<style>
  :root {
    --hero-grey: #a7a7a7;
    --hero-photo-top: #9c9c9c;
    --hero-photo-bottom: #929292;
    --brand-green: #3f8a16;
    --ink: #111111;
    --body-grey: #555555;
    --white: #ffffff;
    --footer-black: #121212;
    --rule: #4a4a4a;
  }
  * { box-sizing: border-box; margin: 0; padding: 0; }
  html, body { width: 1063px; height: 1200px; overflow: hidden; background: var(--white); }
  body { position: relative; font-family: "Roboto", Arial, sans-serif; }

  .hero-shape, .footer-shape { position: absolute; left: 0; top: 0; width: 1063px; height: 1200px; pointer-events: none; }

  .brand { position: absolute; left: 99px; top: 34px; display: flex; align-items: center; gap: 8px; }
  .brand-dot { width: 22px; height: 22px; border-radius: 50%; background: var(--brand-green); }
  .brand-name { font-weight: 700; font-size: 22px; color: var(--brand-green); letter-spacing: .5px; }

  .main-nav { position: absolute; right: 98px; top: 48px; display: flex; gap: 27px; }
  .main-nav a { color: var(--white); text-decoration: none; font-weight: 700; font-size: 13.5px; letter-spacing: .1px; }

  .scroll-ring { position: absolute; left: 480px; top: 348px; width: 102px; height: 102px; border: 1.5px solid var(--white); border-radius: 50%; }
  .scroll-button { position: absolute; left: 502px; top: 370px; width: 58px; height: 58px; border-radius: 50%; background: var(--white); box-shadow: 0 3px 8px rgba(0,0,0,.25); display: flex; align-items: center; justify-content: center; }

  .intro { position: absolute; left: 100px; top: 486px; width: 863px; text-align: center; }
  .intro h1 { font-family: "Work Sans", Arial, sans-serif; font-weight: 800; font-size: 28px; line-height: 37px; color: var(--ink); letter-spacing: .3px; margin-bottom: 25px; }
  .intro p { font-size: 13.6px; line-height: 23px; color: var(--body-grey); margin-bottom: 13px; }
  .intro .source-link { color: var(--brand-green); text-decoration: underline; display: block; padding: 0 30px; margin-bottom: 19px; font-size: 13.6px; line-height: 23px; }

  .footer-brand { position: absolute; left: 0; width: 1063px; top: 1056px; display: flex; justify-content: center; align-items: center; gap: 8px; }
  .footer-brand .brand-dot { background: var(--white); }
  .footer-brand .brand-name { color: var(--white); }
  .footer-rule { position: absolute; left: 99px; top: 1146px; width: 865px; height: 1px; background: var(--rule); }
  .copyright { position: absolute; left: 0; width: 1063px; top: 1159px; text-align: center; color: var(--white); font-size: 12.5px; }
  .legal-links { position: absolute; right: 99px; top: 1159px; color: var(--white); font-size: 12.5px; }
  .legal-links a { color: var(--white); text-decoration: none; }
  .legal-links span { margin: 0 10px; }
</style>
</head>
<body>
  <svg class="hero-shape" viewBox="0 0 1063 1200">
    <defs>
      <linearGradient id="heroPhotoTone" x1="0" y1="0" x2="0" y2="1">
        <stop offset="0" stop-color="var(--hero-photo-top)"/>
        <stop offset="1" stop-color="var(--hero-photo-bottom)"/>
      </linearGradient>
      <clipPath id="heroClip"><path d="M0,0 H1063 V272 Q531,523 0,272 Z"/></clipPath>
    </defs>
    <path d="M0,0 H1063 V275 Q531,541 0,275 Z" fill="var(--brand-green)"/>
    <path d="M0,0 H1063 V272 Q531,523 0,272 Z" fill="var(--hero-grey)"/>
    <rect x="360" y="30" width="346" height="327" rx="6" fill="url(#heroPhotoTone)" clip-path="url(#heroClip)" role="img" aria-label="Photo of a signpost with arrows reading inequality, disparity, unfairness and injustice"/>
  </svg>

  <svg class="footer-shape" viewBox="0 0 1063 1200" aria-hidden="true">
    <path d="M0,1100 Q531,830 1063,1100 V1200 H0 Z" fill="var(--brand-green)"/>
    <path d="M0,1103 Q531,847 1063,1103 V1200 H0 Z" fill="var(--footer-black)"/>
  </svg>

  <header>
    <div class="brand"><span class="brand-dot"></span><span class="brand-name">NVOB</span></div>
    <nav class="main-nav">
      <a href="#">HOME</a>
      <a href="#">AUDIT RESULTS</a>
      <a href="#">RECOMMENDATIONS</a>
      <a href="#">BLOG</a>
      <a href="#">CONTACT US</a>
    </nav>
  </header>

  <div class="scroll-ring"></div>
  <a class="scroll-button" href="#intro" aria-label="Scroll down">
    <svg width="20" height="20" viewBox="0 0 20 20"><path d="M10 3 V15 M4 10 L10 16 L16 10" fill="none" stroke="var(--brand-green)" stroke-width="3.2" stroke-linecap="round" stroke-linejoin="round"/></svg>
  </a>

  <main class="intro" id="intro">
    <h1>WISCONSIN’S NON-UNIFORM<br>PROPERTY TAX PROBLEM</h1>
    <p>Article VIII Section 1 of the State Constitution states that all taxation shall be uniform. Non-uniform taxation is a statewide epidemic. For proof of this, see the results of this watchdog investigation done by the Lakeshore Daily Ledger.</p>
    <a class="source-link" href="#">https://archive.lakeshoreledger.com/watchdog/watchdogreports/across-wisconsin-uneven-property-assessments-fly-in-the-face-of-fairness-<br>418302957.html</a>
    <p>Too many property taxes in the State of Wisconsin are not uniform. Non-uniform taxes are unjust and unfair. The tax burden must be fairly distributed across all property owners.</p>
    <p>Per Wisconsin Statute 73.03, it is actually the Department of Revenue who has the duty and responsibility to oversee the entire assessment process to ensure uniform taxation. However, the Department of Revenue has failed to do this and their leadership is indifferent. Past governors,</p>
    <p>Other organizations have lobbied legislators to tilt property tax administration in their favor.</p>
    <p>All of these things have created the need for the Northmere Valuation Oversight Board.</p>
  </main>

  <footer>
    <div class="footer-brand"><span class="brand-dot"></span><span class="brand-name">NVOB</span></div>
    <div class="footer-rule"></div>
    <p class="copyright">© 2022 NVOB &nbsp;|&nbsp; All Rights Reserved</p>
    <p class="legal-links"><a href="#">Privacy Policy</a><span>|</span><a href="#">Terms &amp; Conditions</a></p>
  </footer>
</body>
</html>
```